Design a Website for an IT Support Company

We are an IT support company that provides commercial IT support and services to small and medium sized businesses. We are in need of a website to be developed for our business.
We would like to work with someone who is either familiar with the IT field, or has developed a website for an IT support company in the past.
Some examples of designs/layouts that we like:
https://www.veldaworks.example/
http://www.marsbyquill.example/
http://817kq.example/
http://www.olbenstructures.example/
http://www.bykq.example/
I have attached a word document that gives a menu system/page layout format that we would like for our website as well as branch office phone numbers. Our logo is also attached that you can use for your design purposes. We currently do not have copy produced for all of the pages outlined in the word document, but would get this done during the project with the selected designer.
We would like the website to be SEO friendly & fully responsive. We would prefer a Wordpress format, however, we are open to HTML formats as well.

```html
<!DOCTYPE html>
<html lang="en">
<head>
<meta charset="utf-8">
<title>Corvane IT</title>
<link href="https://fonts.googleapis.com/css2?family=Poppins:wght@300;400;500;600;700&display=swap" rel="stylesheet">
<style>
:root{
  --blue:#1172c2;
  --blue-deep:#0b4f9a;
  --ink:#222;
  --muted:#555;
  --faint:#9a9a9a;
  --panel:#f7f7f7;
  --white:#fff;
}
*{box-sizing:border-box;margin:0;padding:0}
html,body{width:1200px;height:3180px;overflow:hidden}
body{font-family:'Poppins',sans-serif;color:var(--ink);background:var(--white);position:relative}
ul{list-style:none}
.header{height:97px;display:flex;align-items:center;justify-content:space-between;padding:0 160px 0 170px}
.brand{display:flex;align-items:center;gap:10px;font-family:'Poppins',sans-serif;font-weight:600;font-size:24px;color:var(--blue)}
.brand-dot{width:16px;height:16px;border-radius:50%;background:var(--blue)}
.nav{display:flex}
.nav a{font-size:12px;font-weight:600;color:var(--ink);text-decoration:none;padding:0 24px;position:relative;line-height:40px}
.nav a.active::after{content:"";position:absolute;left:24px;right:24px;bottom:0;height:3px;background:var(--blue)}
.hero{position:relative;height:526px;background:linear-gradient(120deg,#2d3a4d 0%,#5a6f86 45%,#9fb2c4 75%,#7d8fa0 100%);text-align:center;color:var(--white)}
.hero-title{position:absolute;top:238px;left:0;right:0;font-size:29px;font-weight:600}
.hero-sub{position:absolute;top:290px;left:310px;right:310px;font-size:17px;font-weight:400;line-height:29px}
.btn{display:inline-block;background:var(--blue);color:var(--white);font-size:11px;font-weight:600;text-transform:uppercase;border-radius:22px;text-decoration:none;text-align:center}
.hero .btn{position:absolute;top:378px;left:522px;width:156px;line-height:38px}
.dots{position:absolute;top:472px;left:0;right:0;display:flex;justify-content:center;gap:12px}
.dots span{width:6px;height:6px;border-radius:50%;background:rgba(255,255,255,.7)}
.dots span:first-child{background:var(--blue)}
.section-title{text-align:center;color:var(--blue);font-weight:600;font-size:37px}
.services-head{height:127px;padding-top:40px}
.service-row{display:flex}
.service-media{width:600px;position:relative;background:linear-gradient(135deg,#1561b4,#0b4fa2 60%,#1a6bbd);display:flex;flex-direction:column;align-items:center;justify-content:center;color:var(--white)}
.service-media .label{font-size:22px;font-weight:600;margin-top:14px}
.service-body{width:600px;background:var(--panel);padding:0 0 0 32px}
.service-body.left{padding-left:191px}
.service-body h3{color:var(--blue);font-size:24px;font-weight:600;margin-bottom:26px}
.ticks{display:grid;grid-template-columns:218px 290px;row-gap:9px}
.ticks.single{grid-template-columns:340px}
.ticks li{font-size:11px;color:var(--muted);padding-left:28px;position:relative;line-height:18px;white-space:nowrap}
.ticks li::before{content:"";position:absolute;left:2px;top:4px;width:5px;height:9px;border:solid var(--blue);border-width:0 2px 2px 0;transform:rotate(40deg)}
.row-data{height:376px}.row-data .service-body{padding-top:76px}
.row-cloud{height:398px}.row-cloud .service-body{padding-top:86px;background:#fafafa}
.row-voice{height:424px}.row-voice .service-body{padding-top:110px}
.why{height:488px;padding-top:88px;text-align:center}
.rule{width:74px;height:4px;background:var(--blue);margin:24px auto 0}
.why p{margin:34px auto 0;width:860px;font-size:11px;line-height:22px;color:var(--faint);font-weight:300}
.why .btn{margin-top:60px;width:160px;line-height:38px}
.contact{height:447px;display:flex;background:var(--panel)}
.map{width:600px;background:linear-gradient(135deg,#e4e4e4,#cfcfcf 50%,#dcdcdc)}
.contact-body{padding:40px 0 0 36px}
.contact-body h2{color:var(--blue);font-size:37px;font-weight:600}
.contact-body .rule{margin:14px 0 0}
.info{margin-top:36px}
.info li{display:flex;gap:18px;font-size:11px;color:var(--ink);line-height:27px;margin-bottom:24px}
.info svg{flex:none;margin-top:8px}
.contact .btn{width:160px;line-height:38px;margin-top:2px;font-size:11px;text-transform:none}
.footer{height:234px;background:var(--white);position:relative}
.footer .brand{position:absolute;left:170px;top:114px}
.fcol{position:absolute;top:60px}
.fcol h4{font-size:11px;font-weight:600;margin-bottom:20px}
.fcol li{font-size:11px;line-height:29px;color:var(--ink)}
.social{display:flex;gap:8px}
.social span{width:24px;height:24px;border-radius:50%;border:1px solid #9bb6d6}
.bottom{height:63px;border-top:1px solid #e6e6e6;display:flex;align-items:center;justify-content:center;font-size:11px;position:relative}
.bottom .page{position:absolute;right:28px;color:var(--faint)}
</style>
</head>
<body>
<header class="header">
  <div class="brand"><span class="brand-dot"></span>Corvane IT</div>
  <nav class="nav">
    <a class="active" href="#">Home</a>
    <a href="#">Services</a>
    <a href="#">Why Corvane IT ?</a>
    <a href="#">Contact Us</a>
  </nav>
</header>

<section class="hero" role="img" aria-label="Two businessmen in suits talking in a bright office">
  <h1 class="hero-title">Corvane IT</h1>
  <p class="hero-sub">We are an IT support company that provides commercial IT support and services</p>
  <a class="btn" href="#">Learn More</a>
  <div class="dots"><span></span><span></span><span></span><span></span></div>
</section>

<section class="services-head"><h2 class="section-title">Services</h2></section>

<div class="service-row row-data">
  <div class="service-media" role="img" aria-label="Server racks in a data centre under a blue tint">
    <svg width="96" height="120" viewBox="0 0 96 120" fill="none" stroke="#fff" stroke-width="4">
      <ellipse cx="48" cy="18" rx="42" ry="14"/>
      <path d="M6 18v84c0 8 19 14 42 14s42-6 42-14V18"/>
      <path d="M6 46c0 8 19 14 42 14s42-6 42-14M6 74c0 8 19 14 42 14s42-6 42-14"/>
    </svg>
    <div class="label">Data</div>
  </div>
  <div class="service-body">
    <h3>Data</h3>
    <ul class="ticks">
      <li>Managed IT Services</li><li>Servers &amp; Virtualization</li>
      <li>IT Support &amp; Consulting</li><li>Remote Monitoring Services</li>
      <li>IT Helpdesk Services</li><li>Wireless Networking</li>
      <li>Network Security</li><li>Email &amp; Spam Threat Management</li>
      <li>Data Backup &amp; Recovery</li><li>Structured Cabling</li>
    </ul>
  </div>
</div>

<div class="service-row row-cloud">
  <div class="service-body left">
    <h3>Cloud</h3>
    <ul class="ticks single">
      <li>Nimbus Office Migrations</li>
      <li>Skyrack Cloud Management Services</li>
      <li>Cloud Migration Services</li>
      <li>Hosted Virtual Servers</li>
      <li>Hosted Telephone Systems</li>
    </ul>
  </div>
  <div class="service-media" role="img" aria-label="Blue cloud computing backdrop with servers">
    <svg width="150" height="100" viewBox="0 0 150 100" fill="none" stroke="#fff" stroke-width="4">
      <path d="M36 96a32 32 0 0 1-2-64 40 40 0 0 1 76-6 34 34 0 0 1 4 70z"/>
    </svg>
    <div class="label">Cloud</div>
  </div>
</div>

<div class="service-row row-voice">
  <div class="service-media" role="img" aria-label="Man at a desk talking on a headset under a blue tint">
    <svg width="100" height="170" viewBox="0 0 100 170" fill="none" stroke="#fff" stroke-width="4">
      <rect x="22" y="4" width="56" height="100" rx="28"/>
      <path d="M6 80a44 44 0 0 0 88 0M50 124v40M30 166h40"/>
    </svg>
    <div class="label">Voice</div>
  </div>
  <div class="service-body">
    <h3>Voice</h3>
    <ul class="ticks single">
      <li>Starline Consulting</li>
      <li>Business Telephone Systems</li>
      <li>Multiple Office Phone Systems</li>
      <li>Parlo Telephone Systems</li>
      <li>SIP Trunks</li>
    </ul>
  </div>
</div>

<section class="why">
  <h2 class="section-title">Why Corvane IT</h2>
  <div class="rule"></div>
  <p>We keep small and medium sized businesses running with fast local support, clear pricing and engineers who know your systems. From daily helpdesk calls to full network projects, our team plans, installs and monitors everything so your staff can focus on their work, not on the technology behind it, every single day.</p>
  <a class="btn" href="#">Learn More</a>
</section>

<section class="contact">
  <div class="map" role="img" aria-label="Street map of the Houston area"></div>
  <div class="contact-body">
    <h2>Contact Us</h2>
    <div class="rule"></div>
    <ul class="info">
      <li><svg width="10" height="13" viewBox="0 0 10 13"><path d="M5 0a5 5 0 0 0-5 5c0 4 5 8 5 8s5-4 5-8a5 5 0 0 0-5-5z" fill="#1172c2"/><circle cx="5" cy="5" r="2" fill="#fff"/></svg><span>Lindhof Büro<br>Marlenweg 12 | 10400 Berlin</span></li>
      <li><svg width="12" height="9" viewBox="0 0 12 9" fill="none" stroke="#1172c2" stroke-width="1.4"><rect x=".7" y=".7" width="10.6" height="7.6"/><path d="M.7.7 6 5l5.3-4.3"/></svg><span>E-Mail: info@corvane.example</span></li>
      <li><svg width="11" height="11" viewBox="0 0 11 11"><path d="M2 0l2 2.5-1.2 1.5a7 7 0 0 0 4.2 4.2L8.5 7 11 9l-1.5 2A9.5 9.5 0 0 1 0 1.5z" fill="#1172c2"/></svg><span>Houston: 555-014-2270</span></li>
    </ul>
    <a class="btn" href="#">Search Our Location</a>
  </div>
</section>

<footer class="footer">
  <div class="brand"><span class="brand-dot"></span>Corvane IT</div>
  <div class="fcol" style="left:399px"><h4>Quick Links</h4><ul><li>Home</li><li>Services</li><li>Why Corvane IT ?</li><li>Contact Us</li></ul></div>
  <div class="fcol" style="left:653px"><h4>Services</h4><ul><li>Data</li><li>Cloud</li><li>Voice</li></ul></div>
  <div class="fcol" style="left:827px"><h4>Connect With Us</h4><div class="social"><span></span><span></span><span></span><span></span><span></span></div></div>
</footer>
<div class="bottom">© 2017 Company Name &nbsp;|&nbsp; All Rights Reserved<span class="page">05</span></div>
</body>
</html>
```